Creation of a page for funnel

Our company is specialized in insoles and well-being. Our insoles help reduce joint problems, stress or ink to promote weight loss. We need a clean and refined sales page, this one will be used on funnel click. The page should display the values of our product in first: "promote weight loss" in second: "Relieves muscle and joint pain" third: "Increases energy and stress stress". The page must be in the colors of our logo (green) if possible this color: light green: dark green 54c248. It is important to follow this model for the page with totally new and fresh desing: https: // lunar-pebble. uk / qtw-lr Additionnal details for icons Section u: 1: "A unique design based on two types of knowledge" 2: "approved by acupressure expert" "Lose weight" 2: "Increases blood flow and oxygen in your body" 3: "Relieves muscle and joint pain" 4: "Increases energy and reduces stress" Section x: 1: "for men and women" 2: "one size "3:" Adjustable by cutting "Section y: 1:" powerful magnet in tourmaline "2:" for all type of shoes "3:" Flexible and light "4:" Breathable "Section z: 1:" free shipping "2 : "Customer service" 3: "money back guarantee" 4: "safe payment"
Target Market(s)
men and women 35
Number of Pages Required
1 page
Requirements
Must have
- the 5 sections mentioned in description
Nice to have
- some GIF like the funnel

```html
<!DOCTYPE html>
<html lang="en">
<head>
<meta charset="utf-8">
<title>StepWell Insoles</title>
<link href="https://fonts.googleapis.com/css2?family=Montserrat:wght@500;600;700&family=Lato:wght@400;700&display=swap" rel="stylesheet">
<style>
:root{
  --green-dark:#2f9a1a;
  --green:#54c248;
  --green-bright:#74d90a;
  --green-mid:#3db412;
  --grey-bg:#efefef;
  --pill:#ededed;
  --ink:#111;
  --text:#333;
  --strip:#101010;
  --footer:#1c1c1c;
  --white:#fff;
}
*{margin:0;padding:0;box-sizing:border-box}
html,body{width:1200px;height:4345px;overflow:hidden}
body{position:relative;font-family:'Lato',sans-serif;color:var(--text);background:var(--white)}
.abs{position:absolute}
h1,h2,h3,.head{font-family:'Montserrat',sans-serif;color:var(--ink)}

/* header */
.brand{left:90px;top:18px;display:flex;align-items:center;gap:10px}
.brand-dot{width:40px;height:40px;border-radius:50%;background:var(--green)}
.brand-name{font-family:'Montserrat',sans-serif;font-weight:700;font-size:40px;color:#555;line-height:1}
.brand-tag{left:143px;top:64px;font-size:17px;color:#333}
.nav{top:38px;font-family:'Montserrat',sans-serif;font-size:18px;color:#222}

/* hero */
.hero-photo{left:0;top:104px;width:540px;height:440px;background:linear-gradient(180deg,#f4e3d8,#dfe6f5 60%,#f7c06a)}
.hero-title{left:60px;top:600px;width:440px;text-align:center;font-size:45px;font-weight:700;line-height:50px;color:var(--ink)}
.hero-list{left:752px;top:250px;list-style:none}
.hero-list li{color:var(--white);font-size:23px;height:46.5px;display:flex;align-items:center;gap:14px}
.btn-outline{left:760px;top:548px;width:245px;height:69px;border:2px solid var(--white);color:var(--white);font-family:'Montserrat',sans-serif;font-size:22px;display:flex;align-items:center;justify-content:center}

/* funnel */
.pill{background:var(--pill);border-radius:0 50px 50px 0;height:100px}
.step-num{width:78px;height:78px;border-radius:50%;background:var(--white);display:flex;align-items:center;justify-content:center;font-family:'Montserrat',sans-serif;font-weight:700;font-size:34px;color:var(--ink)}
.step-text{font-family:'Montserrat',sans-serif;font-weight:500;font-size:20px;letter-spacing:1px;color:#222;line-height:25px}
.step-icon{width:44px;height:44px;border-radius:50%;background:#d8d8d8}
.btn-pill{left:506px;top:1282px;width:188px;height:54px;border-radius:27px;background:var(--green-dark);color:var(--white);font-family:'Montserrat',sans-serif;font-weight:700;font-size:18px;display:flex;align-items:center;justify-content:center}

/* relieve */
.relieve{left:0;top:1446px;width:1200px;height:622px;background:var(--grey-bg)}
.sec-title{font-size:46px;font-weight:600}
.tick-list{list-style:none}
.tick-list li{display:flex;gap:18px;font-size:18px;color:#333;line-height:27px}

/* benefits */
.label{font-size:22px;color:#333;line-height:31px}

/* daily life */
.daily{left:0;top:2648px;width:1200px;height:610px;background:var(--green-bright)}
.card{top:2843px;width:330px;height:305px;border:8px solid var(--white)}
.card-label{position:absolute;left:2px;right:2px;bottom:2px;height:74px;display:flex;align-items:center;justify-content:center;font-family:'Montserrat',sans-serif;font-size:22px;font-weight:500;background:var(--white);color:#111}

/* features */
.feat-circle{width:144px;height:144px;border:2px solid var(--green-mid);border-radius:50%;display:flex;align-items:center;justify-content:center}
.feat-label{width:260px;text-align:center;font-family:'Montserrat',sans-serif;font-weight:500;font-size:21px;line-height:32px;color:#222}

/* strip + footer */
.strip{left:0;top:3832px;width:1200px;height:130px;background:var(--strip)}
.strip-item{top:3877px;display:flex;align-items:center;gap:14px;color:var(--white);font-family:'Montserrat',sans-serif;font-size:18px}
.footer{left:0;top:3962px;width:1200px;height:383px;background:var(--footer)}
.f-head{top:4058px;color:#ddd;font-size:23px;font-family:'Montserrat',sans-serif}
.f-text{color:#bbb;font-size:14px;line-height:26px}
.f-rule{top:4095px;width:1px;height:170px;background:#3a3a3a}
.social{width:32px;height:32px;border-radius:50%}
</style>
</head>
<body>

<header>
  <div class="abs brand"><span class="brand-dot"></span><span class="brand-name">StepWell</span></div>
  <div class="abs brand-tag">L'essayer c'est l'adopter !</div>
  <nav>
    <a class="abs nav" style="left:738px">How It Works</a>
    <a class="abs nav" style="left:933px">Pricing</a>
    <a class="abs nav" style="left:1070px">FAQ</a>
  </nav>
</header>

<section class="hero">
  <div class="abs hero-photo" role="img" aria-label="Bare feet lifting above a pair of blue and yellow insoles"></div>
  <svg class="abs" style="left:0;top:104px" width="1200" height="676" viewBox="0 0 1200 676">
    <path d="M520 0 C700 140 700 520 410 676 L1200 676 L1200 0 Z" fill="var(--green-bright)"/>
    <path d="M570 0 C760 160 720 520 470 676 L1200 676 L1200 0 Z" fill="var(--green-mid)"/>
  </svg>
  <h1 class="abs hero-title">DISCOVER OUR<br>PPRODUCTS</h1>
  <ul class="abs hero-list">
    <li><svg width="20" height="20" viewBox="0 0 20 20"><rect x="1" y="3" width="15" height="15" fill="none" stroke="#fff" stroke-width="2"/><path d="M4 10l4 4 10-11" fill="none" stroke="#fff" stroke-width="2.5"/></svg>400 Acupoints for each foot</li>
    <li><svg width="20" height="20" viewBox="0 0 20 20"><rect x="1" y="3" width="15" height="15" fill="none" stroke="#fff" stroke-width="2"/><path d="M4 10l4 4 10-11" fill="none" stroke="#fff" stroke-width="2.5"/></svg>Relieve your aches and pains</li>
    <li><svg width="20" height="20" viewBox="0 0 20 20"><rect x="1" y="3" width="15" height="15" fill="none" stroke="#fff" stroke-width="2"/><path d="M4 10l4 4 10-11" fill="none" stroke="#fff" stroke-width="2.5"/></svg>Balance body &amp; mind</li>
    <li><svg width="20" height="20" viewBox="0 0 20 20"><rect x="1" y="3" width="15" height="15" fill="none" stroke="#fff" stroke-width="2"/><path d="M4 10l4 4 10-11" fill="none" stroke="#fff" stroke-width="2.5"/></svg>Reduce stress &amp; anxiety</li>
    <li><svg width="20" height="20" viewBox="0 0 20 20"><rect x="1" y="3" width="15" height="15" fill="none" stroke="#fff" stroke-width="2"/><path d="M4 10l4 4 10-11" fill="none" stroke="#fff" stroke-width="2.5"/></svg>Overweight control</li>
  </ul>
  <a class="abs btn-outline">Shop Now</a>
</section>

<section class="funnel">
  <div class="abs pill" style="left:560px;top:891px;width:478px"></div>
  <div class="abs pill" style="left:520px;top:1012px;width:518px"></div>
  <div class="abs pill" style="left:480px;top:1132px;width:558px"></div>
  <svg class="abs" style="left:0;top:880px" width="1200" height="360" viewBox="0 0 1200 360">
    <path d="M162 11 L632 11 L590 110 L222 110 Z" fill="var(--green-dark)"/>
    <path d="M215 132 L580 132 L542 232 L258 232 Z" fill="#34c80c"/>
    <path d="M270 252 L525 252 L485 352 L310 352 Z" fill="var(--green-bright)"/>
  </svg>
  <div class="abs step-num" style="left:359px;top:902px">01</div>
  <div class="abs step-num" style="left:359px;top:1023px">02</div>
  <div class="abs step-num" style="left:359px;top:1143px">03</div>
  <div class="abs step-text" style="left:650px;top:928px">PROMOTE WEIGHT LOSS</div>
  <div class="abs step-text" style="left:650px;top:1037px">RELIEVES MUSCLE AND<br>JOINT PAIN</div>
  <div class="abs step-text" style="left:650px;top:1157px">INCREASES ENERGY AND<br>REDUCES STRESS</div>
  <div class="abs step-icon" role="img" aria-label="Waist icon" style="left:950px;top:919px"></div>
  <div class="abs step-icon" role="img" aria-label="Knee joint icon" style="left:950px;top:1040px"></div>
  <div class="abs step-icon" role="img" aria-label="Meditation icon" style="left:950px;top:1160px"></div>
  <a class="abs btn-pill">SHOP NOW</a>
</section>

<section>
  <div class="abs relieve"></div>
  <svg class="abs" style="left:560px;top:1446px" width="640" height="622" viewBox="0 0 640 622">
    <path d="M150 0 C20 130 10 470 210 622 L640 622 L640 0 Z" fill="var(--green-bright)"/>
    <path d="M180 0 C60 140 60 480 260 622 L640 622 L640 0 Z" fill="#8a8f95"/>
  </svg>
  <div class="abs" role="img" aria-label="Hand placing an orthopedic insole into a sock-covered foot" style="left:740px;top:1446px;width:460px;height:622px;background:linear-gradient(160deg,#6f767e,#c9c9c9 55%,#2c2c2c)"></div>
  <h2 class="abs sec-title" style="left:90px;top:1605px">Walk to Relieve!</h2>
  <ul class="abs tick-list" style="left:90px;top:1697px">
    <li style="margin-bottom:36px"><svg width="16" height="16" viewBox="0 0 20 20" style="margin-top:5px"><rect x="1" y="3" width="15" height="15" fill="none" stroke="#3db412" stroke-width="2"/><path d="M4 10l4 4 10-11" fill="none" stroke="#3db412" stroke-width="2.5"/></svg><span>A totally natural solution without<br>any health risk</span></li>
    <li style="margin-bottom:36px"><svg width="16" height="16" viewBox="0 0 20 20" style="margin-top:5px"><rect x="1" y="3" width="15" height="15" fill="none" stroke="#3db412" stroke-width="2"/><path d="M4 10l4 4 10-11" fill="none" stroke="#3db412" stroke-width="2.5"/></svg><span>Approved by acupressure expert</span></li>
    <li><svg width="16" height="16" viewBox="0 0 20 20" style="margin-top:5px"><rect x="1" y="3" width="15" height="15" fill="none" stroke="#3db412" stroke-width="2"/><path d="M4 10l4 4 10-11" fill="none" stroke="#3db412" stroke-width="2.5"/></svg><span>A unique design based on two<br>types of knowledge</span></li>
  </ul>
</section>

<section>
  <h2 class="abs sec-title" style="left:0;width:1200px;text-align:center;top:2165px">Walk only 15min per day</h2>
  <svg class="abs" style="left:0;top:2280px" width="1200" height="260" viewBox="0 0 1200 260">
    <g stroke="#bbb" stroke-dasharray="3 3" fill="none">
      <path d="M355 braked"/>
      <path d="M355 28 L415 28 L520 80"/>
      <path d="M360 193 L420 193 L520 140"/>
      <path d="M850 28 L790 28 L680 80"/>
      <path d="M850 195 L790 195 L680 140"/>
    </g>
  </svg>
  <div class="abs" role="img" aria-label="Two green footprints" style="left:520px;top:2290px;width:160px;height:220px;border-radius:50%;background:radial-gradient(circle,#6fd11a,#2f9a1a 70%,transparent 71%)"></div>
  <div class="abs label" style="left:108px;top:2290px">01. lose weight</div>
  <div class="abs label" style="left:108px;top:2446px">02. Increases blood flow<br>and oxygen throughout<br>your body</div>
  <div class="abs label" style="left:800px;top:2278px;width:271px;text-align:right">03.Relieves muscle<br>and joint pain</div>
  <div class="abs label" style="left:780px;top:2446px;width:291px;text-align:right">04. Increases energy<br>and reduces stress</div>
</section>

<section>
  <div class="abs daily"></div>
  <h2 class="abs sec-title" style="left:0;width:1200px;text-align:center;top:2746px;color:var(--white)">Adapted To Your Daily Life!</h2>
  <div class="abs card" role="img" aria-label="Foot stepping onto a blue insole" style="left:90px;border-color:#e85a6b;background:linear-gradient(180deg,#6fa2c8,#e34e62)"><div class="card-label">For men and women</div></div>
  <div class="abs card" role="img" aria-label="Pair of blue insoles" style="left:435px;background:linear-gradient(180deg,#fff,#eef3fb)"><div class="card-label" style="background:var(--green-dark);color:var(--white)">One Size</div></div>
  <div class="abs card" role="img" aria-label="Hands fitting an insole to a foot" style="left:782px;border-color:#e9e3dc;background:linear-gradient(160deg,#f2ece6,#c98d6a)"><div class="card-label">Adjustable by Cutting</div></div>
</section>

<section>
  <h2 class="abs sec-title" style="left:0;width:1200px;text-align:center;top:3356px;line-height:51px">Promotes Safe And Sustainable<br>Weight Loss</h2>
  <div class="abs feat-circle" style="left:116px;top:3500px"><svg width="70" height="70" viewBox="0 0 70 70" fill="none" stroke="#3db412" stroke-width="3"><path d="M48 22 L30 40 a8 8 0 0 1 -12 -12 L36 10"/><path d="M44 6 l8 8 M28 22 l8 8"/></svg></div>
  <div class="abs feat-circle" style="left:390px;top:3500px"><svg width="80" height="50" viewBox="0 0 80 50" fill="none" stroke="#3db412" stroke-width="3"><path d="M6 34 C6 22 16 14 26 14 L36 24 L60 28 C70 30 74 34 74 40 L6 40 Z"/><path d="M6 44 L74 44"/></svg></div>
  <div class="abs feat-circle" style="left:666px;top:3500px"><svg width="70" height="70" viewBox="0 0 70 70" fill="none" stroke="#3db412" stroke-width="3"><path d="M35 20 L48 32 L35 44 L22 32 Z"/><path d="M22 42 L35 54 L48 42"/><path d="M10 10 l10 10 M10 10 h8 M10 10 v8 M60 10 l-10 10 M60 10 h-8 M60 10 v8 M10 60 l10 -10 M10 60 h8 M10 60 v-8 M60 60 l-10 -10 M60 60 h-8 M60 60 v-8"/></svg></div>
  <div class="abs feat-circle" style="left:940px;top:3500px"><svg width="70" height="70" viewBox="0 0 70 70" fill="none" stroke="#3db412" stroke-width="3"><path d="M20 30 q-5 -6 0 -12 q5 -6 0 -12 M35 30 q-5 -6 0 -12 q5 -6 0 -12 M50 30 q-5 -6 0 -12 q5 -6 0 -12"/><path d="M10 38 H60 M10 44 H60"/><path d="M20 52 l4 10 M35 52 v10 M50 52 l-4 10"/></svg></div>
  <div class="abs feat-label" style="left:58px;top:3672px">Powerful Magnet in<br>Tourmaline</div>
  <div class="abs feat-label" style="left:335px;top:3672px">For all Type of<br>Shoes</div>
  <div class="abs feat-label" style="left:609px;top:3672px">Flexible and light</div>
  <div class="abs feat-label" style="left:883px;top:3672px">Breathable</div>
</section>

<section>
  <div class="abs strip"></div>
  <div class="abs strip-item" style="left:95px"><svg width="48" height="30" viewBox="0 0 48 30" fill="none" stroke="#fff" stroke-width="2"><path d="M14 4 H34 V22 H14 Z M34 10 H42 L46 16 V22 H34"/><circle cx="20" cy="24" r="4"/><circle cx="40" cy="24" r="4"/><path d="M2 10 H10 M4 16 H10"/></svg>Free Shipping</div>
  <div class="abs strip-item" style="left:360px"><svg width="38" height="36" viewBox="0 0 38 36" fill="none" stroke="#fff" stroke-width="2"><circle cx="19" cy="18" r="12"/><path d="M5 16 v6 M33 16 v6"/><text x="11" y="22" font-size="10" fill="#fff" stroke="none">24</text></svg>Customer Service</div>
  <div class="abs strip-item" style="left:614px"><svg width="34" height="34" viewBox="0 0 34 34" fill="none" stroke="#fff" stroke-width="2"><path d="M4 14 H10 V30 H4 Z M10 16 L16 4 C20 4 20 8 19 12 H28 C31 12 31 16 30 18 L27 28 C26 30 24 30 22 30 H10"/></svg>Money Back Guarantee</div>
  <div class="abs strip-item" style="left:928px"><svg width="46" height="40" viewBox="0 0 46 40" fill="none" stroke="#fff" stroke-width="2"><circle cx="28" cy="12" r="8"/><path d="M2 24 H10 V38 H2 Z M10 26 H24 C28 26 28 30 24 30 H16 M10 36 H30 L42 26 C40 22 36 24 34 26"/></svg>Safe Payment</div>
</section>

<footer>
  <div class="abs footer"></div>
  <div class="abs f-head" style="left:88px">Contact Us</div>
  <div class="abs f-text" style="left:88px;top:4110px;line-height:20px">COMPANY<br><span style="font-size:12px">14 Fernhill Road. Eastbay 2710</span></div>
  <div class="abs f-text" style="left:88px;top:4167px;line-height:20px">EMAIL ADDRESS<br><span style="font-size:12px">hello@stepwell.example</span></div>
  <div class="abs f-text" style="left:88px;top:4225px;line-height:20px">CALL US<br><span style="font-size:12px">+ 1 0000 555 01234</span></div>
  <div class="abs f-rule" style="left:370px"></div>
  <div class="abs f-head" style="left:420px">Links</div>
  <div class="abs f-text" style="left:423px;top:4105px">How It Work<br>Pricing<br>Faq</div>
  <div class="abs f-rule" style="left:580px"></div>
  <div class="abs f-head" style="left:641px">Legal</div>
  <div class="abs f-text" style="left:643px;top:4105px">Support<br>Sitemap<br>Contact Us</div>
  <div class="abs f-rule" style="left:767px"></div>
  <div class="abs f-head" style="left:828px">Newsletter</div>
  <div class="abs f-text" style="left:830px;top:4107px;line-height:21px">For exclusive news and updates sign<br>up for our newsletter.</div>
  <div class="abs" style="left:830px;top:4165px;width:243px;height:40px;background:var(--white);font-size:11px;color:#999;padding:13px 14px">Email Address</div>
  <div class="abs" style="left:1073px;top:4165px;width:42px;height:40px;background:var(--green-dark);display:flex;align-items:center;justify-content:center"><svg width="18" height="18" viewBox="0 0 18 18"><path d="M2 9 L16 2 L12 16 L9 10 Z" fill="#fff"/></svg></div>
  <div class="abs social" aria-label="Social link" style="left:832px;top:4232px;background:#3b5998"></div>
  <div class="abs social" aria-label="Social link" style="left:879px;top:4232px;background:#e02a20"></div>
  <div class="abs social" aria-label="Social link" style="left:926px;top:4232px;background:#dc4a38"></div>
  <div class="abs social" aria-label="Social link" style="left:973px;top:4232px;background:#1da1f2"></div>
  <div class="abs social" aria-label="Social link" style="left:1020px;top:4232px;background:#2a7fc0"></div>
  <div class="abs" style="left:0;top:4310px;width:1200px;text-align:center;font-size:11px;color:#bbb">© 2019 Copyrights.STEPWELL.All Rights Reserved</div>
</footer>

</body>
</html>
```